Maplecrest Disability - Social Security Disability Attorneys

Our company is expanding to attract clients nationwide for our social security disability practice. We have a logo, but I am looking for a creative and elegant letterhead that projects an image of being technologically advanced but still professional enough for the legal field. I am looking for the "wow factor" combined with this is still professional enough for a law practice.

Requesting letterhead and business card design
Updates

Had to update and change the logo. The previous logo had a typo. Please send updates with the new logo for consideration. The letterhead and business cards should be professional enough to be used for a law firm. Thanks.

Industry/Entity Type

Law Practice, Law Firm, Healthcare Industry, Government

Colors

Designer to choose colors to be used in the design.

Requirements
Nice to have
• **Please create a vertical design for the business card**

```html
<!DOCTYPE html>
<html lang="en">
<head>
<meta charset="utf-8">
<title>Maplecrest Disability – Business Card</title>
<link rel="stylesheet" href="https://fonts.googleapis.com/css2?family=Cinzel:wght@600&family=Quicksand:wght@500;600&display=swap">
<style>
  :root {
    --backdrop: #a9a9a9;
    --card: #323234;
    --card-back: #2a2a2b;
    --edge: #1a6cf0;
    --blue: #1e78ee;
    --orange: #f07a12;
    --text-light: #e6e6e6;
    --divider: #8a8a8a;
  }
  * { box-sizing: border-box; margin: 0; padding: 0; }
  html, body { width: 1200px; height: 800px; overflow: hidden; }
  body {
    background: var(--backdrop);
    display: flex;
    align-items: center;
    justify-content: center;
    gap: 60px;
    font-family: "Quicksand", sans-serif;
  }
  .card {
    width: 500px;
    height: 286px;
    border-radius: 22px;
    box-shadow: 0 0 0 3px var(--edge), 0 14px 30px rgba(0,0,0,0.3);
    position: relative;
    overflow: hidden;
  }
  .card--contact {
    background: var(--card);
    display: flex;
    align-items: center;
    padding: 0 12px;
  }
  .card--brand {
    background: var(--card-back);
    display: flex;
    align-items: center;
    justify-content: center;
  }

  .identity { flex: none; width: 218px; text-align: right; padding-right: 18px; }
  .identity__name {
    font-family: "Cinzel", serif;
    font-weight: 600;
    font-size: 18px;
    color: var(--blue);
    white-space: nowrap;
  }
  .identity__title { color: var(--orange); font-size: 14px; font-weight: 500; margin-top: 2px; white-space: nowrap; }

  .divider { flex: none; width: 1px; height: 100px; background: var(--divider); }

  .contact { list-style: none; padding-left: 18px; }
  .contact__item {
    display: flex;
    align-items: flex-start;
    gap: 9px;
    color: var(--text-light);
    font-size: 12px;
    font-weight: 500;
    line-height: 1.45;
    margin-bottom: 3px;
    white-space: nowrap;
  }
  .contact__icon { width: 12px; height: 12px; flex: none; margin-top: 3px; }

  .brand-name {
    font-family: "Quicksand", sans-serif;
    font-weight: 600;
    font-size: 30px;
    color: var(--text-light);
    letter-spacing: 0.5px;
    margin-top: 40px;
  }
</style>
</head>
<body>
  <section class="card card--contact" aria-label="Business card, contact side">
    <div class="identity">
      <p class="identity__name">Daniel Whitmore</p>
      <p class="identity__title">Founder &amp; CEO</p>
    </div>
    <div class="divider"></div>
    <ul class="contact">
      <li class="contact__item">
        <svg class="contact__icon" viewBox="0 0 16 16"><path d="M8 1a5 5 0 0 0-5 5c0 3.5 5 9 5 9s5-5.5 5-9a5 5 0 0 0-5-5zm0 7a2 2 0 1 1 0-4 2 2 0 0 1 0 4z" fill="var(--blue)"/></svg>
        <span>4120 Cedar Hollow Road<br>Juneau, Alaska 99801</span>
      </li>
      <li class="contact__item">
        <svg class="contact__icon" viewBox="0 0 16 16"><path d="M4 1l3 3-2 2c1 2 3 4 5 5l2-2 3 3-2 3C7 15 1 9 1 3z" fill="var(--blue)"/></svg>
        <span>555-210-4871</span>
      </li>
      <li class="contact__item">
        <svg class="contact__icon" viewBox="0 0 16 16"><rect x="4" y="1" width="8" height="14" rx="1.5" fill="none" stroke="var(--blue)" stroke-width="1.6"/></svg>
        <span>555-210-4872</span>
      </li>
      <li class="contact__item">
        <svg class="contact__icon" viewBox="0 0 16 16"><rect x="1" y="3" width="14" height="10" rx="1" fill="var(--blue)"/><path d="M1.5 3.5L8 9l6.5-5.5" fill="none" stroke="var(--card)" stroke-width="1.3"/></svg>
        <span>info@maplecrestdisability.com</span>
      </li>
      <li class="contact__item">
        <svg class="contact__icon" viewBox="0 0 16 16"><circle cx="8" cy="8" r="6.5" fill="none" stroke="var(--blue)" stroke-width="1.5"/><path d="M1.5 8h13M8 1.5c-3 3.5-3 9.5 0 13M8 1.5c3 3.5 3 9.5 0 13" fill="none" stroke="var(--blue)" stroke-width="1.1"/></svg>
        <span>maplecrestdisability.com</span>
      </li>
    </ul>
  </section>

  <section class="card card--brand" aria-label="Business card, brand side">
    <p class="brand-name">Maplecrest Disability</p>
  </section>
</body>
</html>
```